Electronics Recycling and IT Asset Disposition Flyer and Brochure Design

We need a 2 side A5 Flyer and 4 side A4 folder( brochure) for our electronics waste recycling and IT asset management and disposition business.
Our business provides free electronics waste recycling for companies, schools, learning institutions,councils, IT companies and government sectors. Many people are ignorant of responsible recycling of electronics which could harm our health if not treated properly.
The list of other services attached in the pdf.
We provide an end to end and tailored solution for our customers from collection, logistics, data sanitisation, remarketing and recycling.

The Flyer should create awareness of responsible electronics recycling and drive the audience to contact us or go to our website to learn more about the company and services.A brief list of services should also be included in the flyer.The goal is to get the audience to contact us to enquire more about our services.

The Brochure should include all the above plus provide more details about the company, processes, services,contact details (fb, linkedin,Twitter). The goal is to convert the audience to customers for recycling and provide other services as added services.

The final design for both flyer and brochure should communicate responsible recycling of electronic scrap and tailored solution for every organisation.

The company website is www.kelvane-scrap.com.au based in Australia. We serve clients nationwide.

Target Market(s)

IT companies, Corporate, schools and learning institutions, government sector

Industry/Entity Type

Recycling

Contact Information for Business Card

Name: Harold Pendrake
email: harold@kelvane-scrap.com.au
website: www.kelvane-scrap.com.au
mobile: +614 612 39057
Phone: 1300 46 2735

Font styles to use
Serif

Requirements
Must have
• I would like the designs to have more images and icons
Nice to have
Should not have
• none

```html
<!DOCTYPE html>
<html lang="en">
<head>
<meta charset="utf-8">
<title>Kelvane Scrap – Service Offering Flyer</title>
<link rel="stylesheet" href="https://fonts.googleapis.com/css2?family=PT+Sans:ital,wght@0,400;0,700;1,400&family=PT+Sans+Narrow:wght@700&display=swap">
<style>
  :root {
    --page-bg: #d9d9d9;
    --ink-dark: #262626;
    --paper: #f3f3f3;
    --green: #4cae1e;
    --green-deep: #2d9410;
    --green-bright: #5fd01c;
    --bullet-green: #1f8f45;
    --text: #2a2a2a;
    --white: #ffffff;
  }
  * { box-sizing: border-box; margin: 0; padding: 0; }
  html, body {
    width: 1200px; height: 1200px; overflow: hidden;
    background: var(--page-bg);
  }
  .flyer {
    position: absolute; left: 192px; top: 22px;
    width: 755px; height: 1071px;
    transform: scale(1.08); transform-origin: top left;
    background: var(--paper);
    overflow: hidden;
    font-family: "PT Sans", sans-serif;
    color: var(--text);
  }
  .flyer-art { position: absolute; inset: 0; }
  .brand {
    position: absolute; left: 50px; top: 160px;
    display: flex; align-items: center; gap: 10px;
    font-family: "PT Sans Narrow", sans-serif; font-weight: 700;
    font-size: 44px; color: var(--green); white-space: nowrap;
  }
  .brand-dot { width: 18px; height: 18px; border-radius: 50%; background: var(--green); }
  .service { position: absolute; }
  .service h2 {
    font-family: "PT Sans Narrow", sans-serif; font-weight: 700;
    font-size: 22px; line-height: 27px; color: var(--green);
    margin-bottom: 10px;
  }
  .service ul { list-style: none; }
  .service li {
    position: relative; padding-left: 25px;
    font-style: italic; font-size: 16.5px; line-height: 23px;
  }
  .service li::before {
    content: ""; position: absolute; left: 2px; top: 6px;
    width: 11px; height: 11px; border-radius: 50%; background: var(--bullet-green);
  }
  .service li.sub { padding-left: 20px; }
  .service li.sub::before { display: none; }
  .service li.sub span { color: var(--bullet-green); font-style: normal; margin-right: 2px; }
  .service li.plain::before { display: none; }
  .collection { left: 42px; top: 393px; width: 300px; }
  .erasure { left: 387px; top: 393px; width: 350px; }
  .on-green h2 { color: var(--white); font-size: 23px; }
  .on-green li { color: var(--white); font-size: 16px; line-height: 22px; }
  .on-green li::before { background: var(--white); }
  .audit { left: 48px; top: 678px; width: 300px; }
  .audit h2 { margin-bottom: 28px; }
  .remarketing { left: 395px; top: 677px; width: 315px; }
  .remarketing ul { margin-bottom: 6px; }
  .footer-text {
    position: absolute; left: 55px; top: 1027px;
    font-family: "PT Sans Narrow", sans-serif; font-weight: 700;
    font-size: 20px; color: var(--ink-dark); white-space: nowrap;
  }
</style>
</head>
<body>
<main class="flyer">
  <svg class="flyer-art" viewBox="0 0 755 1071" width="755" height="1071" aria-hidden="false">
    <defs>
      <linearGradient id="photoTone" x1="0" y1="0" x2="0" y2="1">
        <stop offset="0" stop-color="#ffffff"/>
        <stop offset="0.45" stop-color="#b9c4cc"/>
        <stop offset="0.7" stop-color="#6f8a45"/>
        <stop offset="1" stop-color="#d9dcdf"/>
      </linearGradient>
      <linearGradient id="boxGreen" x1="0" y1="0" x2="1" y2="1">
        <stop offset="0" stop-color="var(--green-deep)"/>
        <stop offset="1" stop-color="var(--green-bright)"/>
      </linearGradient>
    </defs>
    <!-- header -->
    <rect class="header-white" x="0" y="0" width="755" height="300" fill="#ffffff"/>
    <polygon class="header-photo" role="img" aria-label="Photo: light bulb holding a tree on a grassy field, wind turbines in the background"
      points="312,0 755,0 755,238 376,292" fill="url(#photoTone)"/>
    <polygon class="header-dark" points="0,0 302,0 368,293 755,265 755,290 0,352" fill="var(--ink-dark)"/>
    <polygon class="header-band" points="376,292 755,238 755,265 368,294" fill="var(--green)"/>
    <polygon class="header-stripe" points="0,338 755,280 755,286 0,352" fill="var(--green)"/>
    <line class="header-arrow" x1="304" y1="42" x2="370" y2="292" stroke="var(--green)" stroke-width="9"/>
    <polygon class="header-arrow-head" points="300,12 282,48 330,40" fill="var(--green)"/>
    <!-- column divider -->
    <line x1="367" y1="380" x2="367" y2="610" stroke="#e2e2e2" stroke-width="2"/>
    <!-- green services box -->
    <path class="services-box" d="M80,640 H725 V880 Q725,953 650,953 H30 V690 Q30,640 80,640 Z"
      fill="url(#boxGreen)" stroke="var(--ink-dark)" stroke-width="3"/>
    <line x1="367" y1="660" x2="367" y2="940" stroke="rgba(255,255,255,0.18)" stroke-width="2"/>
    <!-- footer -->
    <rect class="footer-dark" x="0" y="1003" width="755" height="68" fill="var(--ink-dark)"/>
    <polygon class="footer-green" points="0,1011 640,1011 675,1071 0,1071" fill="var(--green)"/>
  </svg>

  <div class="brand"><span class="brand-dot"></span>Kelvane Scrap</div>

  <section class="service collection">
    <h2>Secure E-Waste Collection Service</h2>
    <ul>
      <li>Kelvane Scrap collects electronic waste from schools, businesses, home users and government departments</li>
      <li>Secure collection includes pick up of e-waste and transportation to our recycling facility in a secured truck</li>
      <li>Registration of assets and reporting</li>
    </ul>
  </section>

  <section class="service erasure">
    <h2>Certified Data Erasure Services</h2>
    <ul>
      <li>To provide secure data destruction:</li>
      <li class="sub"><span>*</span>X1 pass</li>
      <li class="sub"><span>*</span>X3 pass (Recommended, DoD standard)</li>
      <li class="sub"><span>*</span>X7 pass</li>
      <li>Total destruction of HDDs by degaussing</li>
      <li>Total physical destruction of any storage media by shredding</li>
    </ul>
  </section>

  <section class="service on-green audit">
    <h2>Receipting Registration,<br>Test &amp; Audit Services</h2>
    <ul>
      <li>Registering your assets on our Asset Management System</li>
      <li>Test, audit and verify specifications, condition and resale value</li>
      <li class="plain">Provide a detailed asset report</li>
      <li>Cleaning and removal of company logos and asset tags</li>
    </ul>
  </section>

  <section class="service on-green remarketing">
    <h2>IT Asset Remarketing</h2>
    <ul>
      <li>Recover client’s IT asset and mobile devices for valuation and remarketing</li>
    </ul>
    <h2>Processing &amp; recycling of<br>electronic waste</h2>
    <ul>
      <li>All assets with no market value will be processed as E-Waste and recycled with zero to landfill in our ISO certified partner refinery overseas for metal recovery</li>
    </ul>
  </section>

  <p class="footer-text">Kelvane Scrap | 18-22 Foundry Lane, Ashbury Park 2160 NSW | Service Offering</p>
</main>
</body>
</html>
```